Trade Show Design

Two, doublesided backdrops/one doublesided banner/one countertop. I have 3 sample pictures of the 3 items that we are purchasing and all the dimensions are listed on the file names.
website: www.brickwisestudio.net
We are a training center that teaches homeowner's how to do their own home renovations through in-person classes with hands-on training.
We are looking to update our tradeshow displays utilizing stock photos as our photos do not have high enough resolution. I have attached lots of example pictures to select from but some of my favourites that I want to use are over 10 MB so they won't upload. Will have to figure out a different way to upload. Our tagline is tackle any project like a pro. We also use words such as "learn to reno" or "practical, hands-on training". We want to use our current branding (pictures of our minivan are uploaded as well) and our color palette document and really show people what we are all about - classes that people can attend so they can learn to reno their home.
Updates

For the 2 backdrops, we would like them to either be stand-alone or together incase we go to a trade show and only have room for 1 of them. They are to be different designs, front and back but a continuous flow if we are to use them together. Again, I have to figure out how to upload additional pictures as some of the ones I want to use are larger. Thanks!

Same with the Banner that is also double-sided - this is to be a different design for the back and front. We want minimal wording on everything but we really want to showcase what we do so that people can figure it out quickly when they walk by our booth....we offer in-person class with hands-on training. Learn to do by doing. Like on our vehicle that I sent example pictures of, we can put a list of a few topics so that people can understand:
Renovation Topics:
Bathroom
Drywall
Flooring
Tiling
Basement
Framing
Plumbing
Baseboards
Feature Walls

Here is the link to the Vornel Box to additional photos.

https://files.vornelbox.net/shared/7QK4r_mz2-TX8LwBnPe5YuJsdA0fGhRkZ?view=open

Thanks,
Marla

```html
<!DOCTYPE html>
<html lang="en">
<head>
<meta charset="utf-8">
<title>Brickwise Studio – Trade Show Displays</title>
<link href="https://fonts.googleapis.com/css2?family=Anton&family=Poppins:wght@300;400;600;700;800&display=swap" rel="stylesheet">
<style>
  :root{
    --stage:#272727;
    --teal:#165e6a;
    --orange:#d4962e;
    --stone:#9b9a8a;
    --sky:#a9c6e8;
    --cream:#dfe0ae;
    --tan:#ddd9c7;
    --white:#ffffff;
  }
  *{box-sizing:border-box;margin:0;padding:0}
  html,body{width:967px;height:1200px;overflow:hidden;background:var(--stage)}
  .board{position:relative;width:967px;height:1200px;background:var(--stage);font-family:"Poppins",sans-serif}

  .piece{position:absolute;overflow:hidden}
  .backdrop{width:687px;height:538px;left:59px}
  .backdrop--front{top:53px}
  .backdrop--back{top:609px}
  .banner{width:144px;height:538px;left:764px;background:var(--white)}
  .banner--front{top:53px}
  .banner--back{top:609px}

  .tile{position:absolute;display:flex;flex-direction:column;align-items:center;justify-content:center;text-align:center}
  .photo{position:absolute}
  .photo--warm{background:linear-gradient(150deg,#d9cfc3,#8a7a66 60%,#4f4a44)}
  .photo--workshop{background:linear-gradient(160deg,#8c7a68,#5d6470 55%,#3b3a3a)}
  .photo--bright{background:linear-gradient(140deg,#efeae4,#b9a79a 55%,#6c5b55)}
  .photo--room{background:linear-gradient(170deg,#e8e3dc,#a9958a 50%,#4b4a55)}

  .topics{font-weight:700;font-size:13px;line-height:18.5px;letter-spacing:.1px}
  .topics--white{color:var(--white)}
  .topics--teal{color:var(--teal)}
  .icon{display:block;margin-bottom:14px}

  .brand{display:flex;flex-direction:column;align-items:flex-start}
  .brand__name{display:flex;align-items:center;gap:6px;font-weight:800;font-size:17px;letter-spacing:.3px;line-height:1}
  .brand__mark{width:12px;height:12px;background:var(--orange)}
  .brand__tag{font-weight:300;font-size:9px;margin-top:5px}

  .headline{font-family:"Anton",sans-serif;line-height:1;letter-spacing:-.5px}

  .link-pill{position:absolute;display:flex;align-items:center;height:28px}
  .link-pill__dot{width:28px;height:28px;border-radius:50%;background:var(--orange);display:flex;align-items:center;justify-content:center;position:relative;z-index:1}
  .link-pill__text{background:var(--teal);color:var(--white);font-size:10.5px;height:28px;line-height:28px;padding:0 10px 0 20px;margin-left:-14px;border-radius:0 3px 3px 0}

  .practical{position:absolute;left:0;top:0;width:246px;height:538px;background:linear-gradient(170deg,#d3d2ad,#bdbc90 60%,#a9a981)}
  .practical__line{position:absolute;left:25px;font-family:"Anton",sans-serif;font-size:46px;line-height:1;color:var(--teal)}
  .hands-on{position:absolute;left:26px;top:240px;background:var(--orange);color:var(--white);font-family:"Anton",sans-serif;font-size:40px;line-height:1;padding:8px 12px 10px;transform:rotate(-3deg);border-radius:3px}

  .banner .brand{position:absolute;left:36px}
  .banner .brand__name{font-size:9.5px;gap:4px}
  .banner .brand__mark{width:8px;height:8px}
  .banner .brand__tag{font-size:5px;margin-top:3px}
  .offer{position:absolute;left:0;width:144px;text-align:center;font-family:"Anton",sans-serif;line-height:1}
  .offer__kicker{top:104px;color:var(--orange);font-size:15px}
  .offer__box{position:absolute;left:19px;top:118px;width:108px;height:30px;background:var(--teal);color:var(--white);font-family:"Anton",sans-serif;font-size:21px;line-height:30px;text-align:center;transform:rotate(-3deg)}
  .offer__classes{top:154px;color:var(--sky);font-size:19px}
  .offer__hands{top:176px;color:var(--teal);font-size:16px}
  .mini-topic{position:absolute;left:0;width:144px;text-align:center;font-weight:700;font-size:6.3px;line-height:9.5px}
  .mini-topic svg{display:block;margin:0 auto 4px}
  .mini-topic--teal{color:var(--teal)}
  .mini-topic--orange{color:var(--orange)}
</style>
</head>
<body>
<main class="board">

  <section class="piece backdrop backdrop--front" aria-label="Backdrop front">
    <div class="photo photo--warm" style="left:0;top:0;width:177px;height:187px" role="img" aria-label="Photo of a smiling man and woman in work shirts and tool belts, she holds a cordless drill"></div>

    <div class="tile" style="left:177px;top:0;width:179px;height:187px;background:var(--stone)">
      <div class="brand" style="color:var(--white)">
        <span class="brand__name"><span class="brand__mark"></span>Brickwise Studio</span>
        <span class="brand__tag">Build it right, room by room.</span>
      </div>
    </div>

    <div class="photo photo--bright" style="left:356px;top:0;width:178px;height:187px" role="img" aria-label="Photo of a smiling woman in a plaid shirt swinging a hammer"></div>

    <div class="tile" style="left:534px;top:0;width:153px;height:187px;background:var(--orange)">
      <svg class="icon" width="44" height="38" viewBox="0 0 44 38" aria-hidden="true"><g fill="var(--white)"><rect x="2" y="2" width="28" height="12" rx="3"/><rect x="30" y="6" width="8" height="4"/><rect x="38" y="7" width="5" height="2"/><path d="M8 14h12l-2 12H10z"/><rect x="6" y="27" width="16" height="9" rx="2"/></g></svg>
      <p class="topics topics--white">DRYWALL<br>FEATURE WALLS<br>FRAMING</p>
    </div>

    <div class="tile" style="left:0;top:187px;width:177px;height:187px;background:var(--stone)">
      <svg class="icon" width="42" height="42" viewBox="0 0 42 42" aria-hidden="true"><path d="M6 40V14a10 10 0 0 1 10-10h2" fill="none" stroke="var(--white)" stroke-width="3.2"/><path d="M12 14a12 12 0 0 1 22 0z" fill="var(--white)"/><g stroke="var(--white)" stroke-width="1.6" stroke-dasharray="2 3"><path d="M16 18l-2 16"/><path d="M21 18l0 18"/><path d="M26 18l3 16"/><path d="M31 17l6 12"/></g></svg>
      <p class="topics topics--white">TILING<br>BATHROOM<br>PLUMBING</p>
    </div>

    <div class="tile" style="left:177px;top:187px;width:357px;height:187px;background:var(--teal)">
      <h1 class="headline" style="color:var(--white);font-size:60px;text-align:center;margin-top:-8px">Learn<br>To Reno</h1>
      <svg width="130" height="20" viewBox="0 0 130 20" style="margin-left:40px" aria-hidden="true"><path d="M2 6C40 2 90 1 127 3 128 6 110 7 95 9 80 11 70 14 68 18" fill="none" stroke="var(--orange)" stroke-width="2" stroke-linecap="round"/></svg>
    </div>

    <div class="tile" style="left:534px;top:187px;width:153px;height:187px;background:var(--sky)">
      <svg class="icon" width="46" height="44" viewBox="0 0 46 44" aria-hidden="true"><g fill="var(--teal)"><rect x="10" y="2" width="5" height="18"/><rect x="18" y="6" width="6" height="14"/><path d="M28 4h4v6h4V4h4v8l-3 3v6h-6v-6l-3-3z"/><path d="M3 20l12-6 12 6h16v22H3z"/></g><rect x="20" y="30" width="16" height="6" fill="var(--sky)"/></svg>
      <p class="topics topics--teal">FLOORING<br>BASEBOARDS<br>BASEMENT</p>
    </div>

    <div class="photo photo--room" style="left:0;top:374px;width:241px;height:164px" role="img" aria-label="Photo of a woman with a spackle knife and a man with a paint roller in a room under renovation"></div>

    <div class="tile" style="left:241px;top:374px;width:212px;height:164px;background:var(--stone)">
      <a class="link-pill" style="position:static" aria-label="www.brickwisestudio.net">
        <span class="link-pill__dot"><svg width="10" height="12" viewBox="0 0 10 12" aria-hidden="true"><path d="M1 1v10l3-3 2 4 2-1-2-4h4z" fill="var(--white)"/></svg></span>
        <span class="link-pill__text">brickwisestudio.net</span>
      </a>
    </div>

    <div class="photo photo--workshop" style="left:453px;top:374px;width:234px;height:164px" role="img" aria-label="Photo of a woman in safety glasses and gloves drilling into a board in a workshop"></div>
  </section>

  <section class="piece banner banner--front" aria-label="Banner front">
    <svg style="position:absolute;left:90px;top:0" width="40" height="42" viewBox="0 0 40 42" aria-hidden="true"><path d="M0 0h40v42L0 30z" fill="var(--tan)"/></svg>
    <div class="brand" style="top:58px;left:36px;color:var(--teal)">
      <span class="brand__name"><span class="brand__mark"></span>Brickwise</span>
      <span class="brand__name" style="margin-top:2px;padding-left:12px">Studio</span>
      <span class="brand__tag">Build it right, room by room.</span>
    </div>
    <p class="offer offer__kicker">We Offer</p>
    <p class="offer__box">IN-PERSON</p>
    <p class="offer offer__classes">CLASSES WITH</p>
    <p class="offer offer__hands">Hands-On Training</p>

    <div class="mini-topic mini-topic--teal" style="top:206px">
      <svg width="24" height="24" viewBox="0 0 42 42" aria-hidden="true"><path d="M6 40V14a10 10 0 0 1 10-10h2" fill="none" stroke="var(--teal)" stroke-width="3.5"/><path d="M12 14a12 12 0 0 1 22 0z" fill="var(--teal)"/><g stroke="var(--teal)" stroke-width="2" stroke-dasharray="2 3"><path d="M16 18l-2 16"/><path d="M21 18v18"/><path d="M26 18l3 16"/></g></svg>
      TILING &nbsp;| &nbsp;BATHROOM<br>PLUMBING
    </div>
    <div class="mini-topic mini-topic--orange" style="top:268px">
      <svg width="22" height="19" viewBox="0 0 44 38" aria-hidden="true"><g fill="var(--orange)"><rect x="2" y="2" width="28" height="12" rx="3"/><rect x="30" y="6" width="12" height="4"/><path d="M8 14h12l-2 12H10z"/><rect x="6" y="27" width="16" height="9" rx="2"/></g></svg>
      DRYWALL &nbsp;| &nbsp;FRAMING<br>FEATURE WALLS
    </div>
    <div class="mini-topic mini-topic--teal" style="top:324px">
      <svg width="24" height="23" viewBox="0 0 46 44" aria-hidden="true"><g fill="var(--teal)"><rect x="10" y="2" width="5" height="18"/><rect x="18" y="6" width="6" height="14"/><path d="M28 4h4v6h4V4h4v8l-3 3v6h-6v-6l-3-3z"/><path d="M3 20l12-6 12 6h16v22H3z"/></g></svg>
      FLOORING &nbsp;| &nbsp;BASEMENT<br>BASEBOARDS
    </div>

    <div style="position:absolute;left:0;top:332px;width:30px;height:110px;background:var(--sky)"></div>
    <div style="position:absolute;left:0;top:373px;width:144px;height:60px;background:var(--tan);clip-path:polygon(0 70%,100% 10%,100% 20%,0 80%)"></div>
    <div class="photo photo--workshop" style="left:0;top:381px;width:144px;height:157px;clip-path:polygon(0 22%,100% 0,100% 100%,0 100%)" role="img" aria-label="Photo of a woman in work gloves measuring a board with a tape measure"></div>
  </section>

  <section class="piece backdrop backdrop--back" aria-label="Backdrop back">
    <div class="practical" role="img" aria-label="Tinted photo of a woman in safety glasses sanding wood in a workshop">
      <div class="brand" style="position:absolute;left:66px;top:100px;color:var(--teal)">
        <span class="brand__name" style="font-size:15px"><span class="brand__mark"></span>Brickwise Studio</span>
        <span class="brand__tag" style="color:var(--teal)">Build it right, room by room.</span>
      </div>
      <p class="practical__line" style="top:198px">Practical,</p>
      <p class="hands-on">Hands-on</p>
      <p class="practical__line" style="top:310px;left:34px">Training.</p>
      <svg style="position:absolute;left:52px;top:372px" width="120" height="10" viewBox="0 0 120 10" aria-hidden="true"><path d="M2 6C40 2 90 2 118 4" fill="none" stroke="var(--orange)" stroke-width="1.8" stroke-linecap="round"/></svg>
      <a class="link-pill" style="left:47px;top:463px" aria-label="www.brickwisestudio.net">
        <span class="link-pill__dot"><svg width="10" height="12" viewBox="0 0 10 12" aria-hidden="true"><path d="M1 1v10l3-3 2 4 2-1-2-4h4z" fill="var(--white)"/></svg></span>
        <span class="link-pill__text">brickwisestudio.net</span>
      </a>
    </div>

    <div class="tile" style="left:246px;top:0;width:221px;height:186px;background:var(--teal)">
      <svg class="icon" width="44" height="38" viewBox="0 0 44 38" aria-hidden="true"><g fill="var(--white)"><rect x="2" y="2" width="28" height="12" rx="3"/><rect x="30" y="6" width="8" height="4"/><rect x="38" y="7" width="5" height="2"/><path d="M8 14h12l-2 12H10z"/><rect x="6" y="27" width="16" height="9" rx="2"/></g></svg>
      <p class="topics topics--white">DRYWALL<br>FEATURE WALLS<br>FRAMING</p>
    </div>

    <div class="tile" style="left:467px;top:0;width:220px;height:186px;background:var(--cream)">
      <svg class="icon" width="46" height="44" viewBox="0 0 46 44" aria-hidden="true"><g fill="var(--teal)"><rect x="10" y="2" width="5" height="18"/><rect x="18" y="6" width="6" height="14"/><path d="M28 4h4v6h4V4h4v8l-3 3v6h-6v-6l-3-3z"/><path d="M3 20l12-6 12 6h16v22H3z"/></g><rect x="20" y="30" width="16" height="6" fill="var(--cream)"/></svg>
      <p class="topics topics--teal">FLOORING<br>BASEBOARDS<br>BASEMENT</p>
    </div>

    <div class="photo photo--bright" style="left:246px;top:186px;width:441px;height:190px" role="img" aria-label="Photo of a man and a woman installing a ceiling light fixture together"></div>

    <div class="photo photo--room" style="left:246px;top:376px;width:221px;height:162px" role="img" aria-label="Photo of a man and a woman laying laminate flooring boards"></div>

    <div class="tile" style="left:467px;top:376px;width:220px;height:162px;background:var(--sky)">
      <svg class="icon" width="40" height="40" viewBox="0 0 42 42" aria-hidden="true"><path d="M6 40V14a10 10 0 0 1 10-10h2" fill="none" stroke="var(--teal)" stroke-width="3.2"/><path d="M12 14a12 12 0 0 1 22 0z" fill="var(--teal)"/><g stroke="var(--teal)" stroke-width="1.6" stroke-dasharray="2 3"><path d="M16 18l-2 16"/><path d="M21 18v18"/><path d="M26 18l3 16"/><path d="M31 17l6 12"/></g></svg>
      <p class="topics topics--teal">TILING<br>BATHROOM<br>PLUMBING</p>
    </div>
  </section>

  <section class="piece banner banner--back" aria-label="Banner back">
    <div class="photo photo--bright" style="left:0;top:0;width:144px;height:214px;clip-path:polygon(0 0,100% 0,100% 100%,0 82%)" role="img" aria-label="Photo of a smiling woman in safety glasses holding a drill against a wall"></div>
    <div class="photo photo--warm" style="left:22px;top:181px;width:99px;height:95px;clip-path:polygon(0 0,100% 25%,100% 100%,0 100%)" role="img" aria-label="Photo of a woman holding two cordless drills"></div>

    <div class="brand" style="top:290px;left:37px;color:var(--teal)">
      <span class="brand__name"><span class="brand__mark"></span>Brickwise</span>
      <span class="brand__name" style="margin-top:2px;padding-left:12px">Studio</span>
      <span class="brand__tag">Build it right, room by room.</span>
    </div>

    <div style="position:absolute;left:0;top:351px;width:50px;height:70px;background:var(--sky)"></div>
    <p class="headline" style="position:absolute;left:19px;top:357px;font-size:32px;color:var(--teal);background:var(--white);padding:0 3px">Learn <span style="color:var(--sky)">To</span></p>
    <p class="headline" style="position:absolute;left:61px;top:394px;font-size:32px;color:var(--orange)">Reno</p>
    <svg style="position:absolute;left:48px;top:432px" width="82" height="6" viewBox="0 0 82 6" aria-hidden="true"><path d="M2 4C30 1 60 1 80 2" fill="none" stroke="var(--orange)" stroke-width="1.4" stroke-linecap="round"/></svg>

    <div class="photo photo--workshop" style="left:0;top:441px;width:144px;height:97px" role="img" aria-label="Photo of a man in safety glasses working on a cabinet in a workshop"></div>
  </section>

</main>
</body>
</html>
```